High end Electrical/home automation Business Card

Need a card for a high end electrical and home automation company utilising the existing logo.
Phone
Email
Website

Like black look with raised detail. Don’t necessarily need to keep colour of logo it could be made grayscale or white etc

Target Market(s)

High end clients

Contact Information for Business Card

Brightmoor Electrical

Requirements
Must have
• Logo, phone, email, website, address

High end look
Nice to have
• Black background card
Raised font
Should not have
• Lots of colour

```html
<!DOCTYPE html>
<html lang="en">
<head>
<meta charset="UTF-8">
<title>Brightmoor Electrical – Business Card</title>
<link href="https://fonts.googleapis.com/css2?family=Roboto:wght@400;500;700&display=swap" rel="stylesheet">
<style>
  :root {
    --backdrop: #9b9b9b;
    --paper: #f7f7f7;
    --ink: #3a3a3c;
    --ink-soft: #5a5a5e;
    --accent: #2a8fcb;
    --card-black: #141416;
    --card-black-raised: #1f1f22;
    --edge-dark: #0a0a0b;
  }
  * { box-sizing: border-box; margin: 0; padding: 0; }
  html, body {
    width: 1200px; height: 1106px; overflow: hidden;
    background: var(--backdrop);
    font-family: "Roboto", Arial, sans-serif;
  }
  .stage {
    position: relative; width: 1200px; height: 1106px;
    display: flex; flex-direction: column; align-items: center; justify-content: center; gap: 70px;
  }
  .card {
    width: 700px; height: 400px; position: relative;
    box-shadow: 0 18px 40px rgba(0,0,0,0.28);
  }
  .card-front {
    background: var(--paper);
    border-bottom: 3px solid var(--edge-dark);
    display: flex; align-items: center; padding: 0 46px;
  }
  .brand {
    display: flex; align-items: center; gap: 12px; width: 262px; flex: none;
  }
  .brand-mark {
    width: 20px; height: 20px; border-radius: 50%; background: var(--ink); flex: none;
  }
  .brand-name {
    font-weight: 700; font-size: 24px; color: var(--ink); line-height: 1.1; white-space: nowrap;
  }
  .divider {
    width: 2px; height: 170px; background: var(--ink); margin: 0 28px 0 22px; flex: none;
  }
  .contact { min-width: 0; }
  .contact-name {
    color: var(--accent); font-size: 26px; font-weight: 400; letter-spacing: 0.5px; text-transform: uppercase; line-height: 1.1;
  }
  .contact-role {
    color: var(--ink-soft); font-size: 18px; margin: 4px 0 16px;
  }
  .contact-list { list-style: none; }
  .contact-list li {
    display: flex; align-items: center; gap: 10px; color: var(--ink); font-size: 16px; line-height: 1.75; white-space: nowrap;
  }
  .contact-list svg { width: 15px; height: 15px; flex: none; fill: var(--ink-soft); }
  .card-back {
    background: var(--card-black);
    border-bottom: 4px solid var(--edge-dark);
    display: flex; align-items: center; justify-content: center;
  }
  .back-name {
    font-weight: 700; font-size: 46px; color: var(--card-black-raised); letter-spacing: 0.5px;
  }
</style>
</head>
<body>
<main class="stage">
  <section class="card card-front">
    <div class="brand">
      <span class="brand-mark"></span>
      <span class="brand-name">Brightmoor Electrical</span>
    </div>
    <div class="divider"></div>
    <div class="contact">
      <p class="contact-name">Owen Hartley</p>
      <p class="contact-role">Partner</p>
      <ul class="contact-list">
        <li>
          <svg viewBox="0 0 24 24" aria-hidden="true"><path d="M6.6 10.8a15.1 15.1 0 0 0 6.6 6.6l2.2-2.2c.3-.3.7-.4 1-.2 1.1.4 2.3.6 3.6.6.6 0 1 .4 1 1V20c0 .6-.4 1-1 1A17 17 0 0 1 3 4c0-.6.4-1 1-1h3.5c.6 0 1 .4 1 1 0 1.3.2 2.5.6 3.6.1.3 0 .7-.2 1z"/></svg>
          443-555-0187
        </li>
        <li>
          <svg viewBox="0 0 24 24" aria-hidden="true"><path d="M2 5h20v14H2z M2 5l10 8 10-8" fill="none" stroke="#5a5a5e" stroke-width="2"/></svg>
          Owen@brightmoorelectrical.com
        </li>
        <li>
          <svg viewBox="0 0 24 24" aria-hidden="true"><circle cx="12" cy="12" r="9" fill="none" stroke="#5a5a5e" stroke-width="2"/><path d="M3 12h18M12 3c3 3 3 15 0 18M12 3c-3 3-3 15 0 18" fill="none" stroke="#5a5a5e" stroke-width="1.6"/></svg>
          www.brightmoorelectrical.com
        </li>
        <li>
          <svg viewBox="0 0 24 24" aria-hidden="true"><path d="M12 2a7 7 0 0 0-7 7c0 5.2 7 13 7 13s7-7.8 7-13a7 7 0 0 0-7-7zm0 9.5a2.5 2.5 0 1 1 0-5 2.5 2.5 0 0 1 0 5z"/></svg>
          18 Harbor Lane, Annapolis, MD
        </li>
      </ul>
    </div>
  </section>
  <section class="card card-back">
    <span class="back-name">Brightmoor Electrical</span>
  </section>
</main>
</body>
</html>
```